Pellmora Business Cards

Create new business cards with the details below.

Stuart Kovan
Director

MB: +61 427 315 964
PH: 1300 647 519
Email: stuart.kovan@pellmora.com.au
Address: 27D Halden Parade, Brookvale VIC 3174 Australia
Website: www.pellmora.com.au

Target Market(s)

Other business

Industry/Entity Type

Business

Requirements
Must have
• must be clean looking

```html
<!DOCTYPE html>
<html lang="en">
<head>
<meta charset="utf-8">
<title>Pellmora Business Cards</title>
<link rel="stylesheet" href="https://fonts.googleapis.com/css2?family=Montserrat:wght@700;800&family=Roboto+Condensed:wght@400;700&display=swap">
<style>
  :root {
    --bg: #ecebe7;
    --card: #ffffff;
    --lime: #a6d21c;
    --lime-light: #c4e53a;
    --charcoal: #2e2e2e;
    --grey: #5a5a5a;
    --ink: #1d1d1d;
  }
  * { margin: 0; padding: 0; box-sizing: border-box; }
  html, body { width: 1200px; height: 913px; overflow: hidden; }
  body { background: var(--bg); position: relative; font-family: "Roboto Condensed", sans-serif; }

  .card {
    position: absolute;
    width: 540px; height: 310px;
    background: var(--card);
    box-shadow: 0 10px 28px rgba(0,0,0,.18);
    overflow: hidden;
  }
  .card--front { left: 50px; top: 140px; }
  .card--back { left: 610px; top: 460px; }
  .card__shapes { position: absolute; inset: 0; width: 100%; height: 100%; }

  .brand { position: absolute; display: flex; align-items: center; gap: 12px; }
  .brand__mark { background: var(--lime); }
  .brand__name {
    font-family: "Montserrat", sans-serif; font-weight: 800;
    color: var(--ink); letter-spacing: 1px; text-transform: uppercase; line-height: 1;
  }
  .brand__tagline {
    font-family: "Montserrat", sans-serif; font-weight: 700;
    color: var(--ink); text-transform: uppercase; letter-spacing: 1.5px; line-height: 1; margin-top: 6px;
  }

  .card--front .brand { left: 110px; top: 112px; }
  .card--front .brand__mark { width: 40px; height: 40px; }
  .card--front .brand__name { font-size: 46px; }
  .card--front .brand__tagline { font-size: 17px; }

  .card--back .brand { left: 34px; top: 92px; }
  .card--back .brand__mark { width: 24px; height: 24px; }
  .card--back .brand__name { font-size: 28px; }
  .card--back .brand__tagline { font-size: 10.5px; margin-top: 4px; }

  .person { position: absolute; right: 40px; top: 34px; text-align: right; }
  .person__name { font-weight: 700; font-size: 17px; color: var(--charcoal); }
  .person__role { font-size: 11px; color: var(--grey); margin-top: 2px; }

  .contact { position: absolute; left: 40px; top: 158px; list-style: none; }
  .contact__item { display: flex; align-items: center; gap: 10px; font-size: 12.5px; color: var(--ink); height: 19px; }
  .contact__item--web { font-weight: 700; }
  .contact__icon { width: 12px; height: 12px; fill: var(--lime); flex: none; }
</style>
</head>
<body>

<section class="card card--front" aria-label="Business card front">
  <svg class="card__shapes" viewBox="0 0 540 310" preserveAspectRatio="none" aria-hidden="true">
    <path d="M300 0 L540 0 L540 14 Q420 6 300 0 Z" fill="var(--charcoal)"/>
    <path d="M360 0 L540 0 L540 7 Q450 3 360 0 Z" fill="var(--lime)"/>
    <path d="M150 310 Q400 270 540 160 L540 310 Z" fill="var(--charcoal)"/>
    <path d="M190 310 Q420 280 540 180 L540 310 Z" fill="var(--lime)"/>
    <path d="M300 310 Q450 290 540 230 L540 310 Z" fill="var(--lime-light)"/>
  </svg>
  <div class="brand">
    <span class="brand__mark"></span>
    <div>
      <div class="brand__name">Pellmora</div>
      <div class="brand__tagline">Plantation Shutters</div>
    </div>
  </div>
</section>

<section class="card card--back" aria-label="Business card back">
  <svg class="card__shapes" viewBox="0 0 540 310" preserveAspectRatio="none" aria-hidden="true">
    <path d="M300 0 L540 0 L540 14 Q420 6 300 0 Z" fill="var(--charcoal)"/>
    <path d="M360 0 L540 0 L540 7 Q450 3 360 0 Z" fill="var(--lime)"/>
    <path d="M200 310 Q420 270 540 150 L540 310 Z" fill="var(--charcoal)"/>
    <path d="M240 310 Q440 280 540 170 L540 310 Z" fill="var(--lime)"/>
    <path d="M340 310 Q470 290 540 225 L540 310 Z" fill="var(--lime-light)"/>
  </svg>

  <div class="person">
    <div class="person__name">Stuart Kovan</div>
    <div class="person__role">Director</div>
  </div>

  <div class="brand">
    <span class="brand__mark"></span>
    <div>
      <div class="brand__name">Pellmora</div>
      <div class="brand__tagline">Plantation Shutters</div>
    </div>
  </div>

  <ul class="contact">
    <li class="contact__item">
      <svg class="contact__icon" viewBox="0 0 12 12"><path d="M6 0a4 4 0 0 1 4 4c0 3-4 8-4 8S2 7 2 4a4 4 0 0 1 4-4zm0 2.5a1.5 1.5 0 1 0 0 3 1.5 1.5 0 0 0 0-3z"/></svg>
      27D Halden Parade, Brookvale VIC 3174 Australia
    </li>
    <li class="contact__item">
      <svg class="contact__icon" viewBox="0 0 12 12"><rect x="3" y="0" width="6" height="12" rx="1.2"/></svg>
      +61 427 315 964
    </li>
    <li class="contact__item">
      <svg class="contact__icon" viewBox="0 0 12 12"><path d="M1 4c0-2 2-3 5-3s5 1 5 3l-2 1-1-2H4L3 5zM2 6h8v5H2z"/></svg>
      1300 647 519
    </li>
    <li class="contact__item">
      <svg class="contact__icon" viewBox="0 0 12 12"><path d="M0 2h12v8H0zM0 2l6 5 6-5" stroke="#fff" stroke-width=".8"/></svg>
      stuart.kovan@pellmora.com.au
    </li>
    <li class="contact__item contact__item--web">
      <svg class="contact__icon" viewBox="0 0 12 12"><circle cx="6" cy="6" r="6"/><path d="M0 6h12M6 0c-3 3-3 9 0 12M6 0c3 3 3 9 0 12" stroke="#fff" stroke-width=".8" fill="none"/></svg>
      www.pellmora.com.au
    </li>
  </ul>
</section>

</body>
</html>
```